Tellmora Corporate Stationery

Look for design of all new corporate stationery for an existing insurance broking business that is going through a redesign and move from older partners to younger family members. New Logo is attached. Company is Brisbane based.
Colours in the Logo is Hex #43bed8 and website features a lot of hex #17b8d8. Website front page "A plan to protect you" - headline. "Professional and Individual advice to protect your greatest assets" - tagline.

Stationery required: Business Cards, Letter head, Thank-you cards, Birthday cards, Presentation folders, With Compliment slips and a powerpoint template. We also would like to send a card to all customers with the something along of the lines of "something new".

Target Market(s)

Customers of Insurance business looking at superannuation, life and income protection insurance, investment advice and wills

Industry/Entity Type

Insurance Broker

Font styles to use
Other font styles liked:
• same as logo

Requirements
Must have
• The above designs for new stationery for the new business including:
• Business Cards, Letter head, Thank-you cards, Birthday cards, Presentation folders, With Compliment slips and a powerpoint template. We also would like to send a card to all customers with the something along of the lines of "something new".
Nice to have
• It is a new look - long time family business being passed to next generation - big focus on advice for YOU, individual advice etc..

```html
<!DOCTYPE html>
<html lang="en">
<head>
<meta charset="utf-8">
<title>Tellmora Business Card</title>
<link href="https://fonts.googleapis.com/css2?family=Open+Sans:wght@400;600&display=swap" rel="stylesheet">
<style>
  :root {
    --page: #e9e7e4;
    --teal-deep: #1d93ad;
    --teal: #43bed8;
    --teal-light: #7fd3e4;
    --slate: #3d4247;
    --frost: rgba(236, 240, 242, 0.82);
    --text-light: #f4fbfd;
    --brand: #17a3c2;
  }
  * { margin: 0; padding: 0; box-sizing: border-box; }
  html, body { width: 1200px; height: 969px; overflow: hidden; }
  body {
    background: var(--page);
    font-family: "Open Sans", Arial, sans-serif;
    position: relative;
  }
  .business-card {
    position: absolute;
    left: 120px; top: 212px;
    width: 960px; height: 546px;
    border-radius: 22px;
    overflow: hidden;
    background: linear-gradient(90deg, var(--teal-deep) 0%, var(--teal) 30%, var(--teal-light) 55%, #b9c6cc 78%, var(--slate) 88%, var(--slate) 100%);
    box-shadow: 0 12px 30px rgba(0,0,0,0.18);
  }
  .frost-disc {
    position: absolute;
    left: 372px; top: -17px;
    width: 580px; height: 580px;
    border-radius: 50%;
    background: radial-gradient(circle at 45% 40%, rgba(255,255,255,0.92), var(--frost) 70%, rgba(220,228,232,0.75));
    border: 2px solid rgba(255,255,255,0.6);
  }
  .contact-block {
    position: absolute;
    left: 45px; top: 108px;
    color: var(--text-light);
  }
  .person-name { font-size: 30px; font-weight: 600; letter-spacing: 0.5px; line-height: 1.2; }
  .person-role { font-size: 23px; font-weight: 400; line-height: 1.3; }
  .address { margin-top: 30px; font-size: 23px; line-height: 1.45; }
  .contact-list { list-style: none; margin-top: 14px; }
  .contact-list li {
    display: flex; align-items: center; gap: 14px;
    font-size: 22px; line-height: 36px;
  }
  .contact-list svg { width: 20px; height: 20px; fill: var(--text-light); flex: none; }
  .brand-name {
    position: absolute;
    left: 372px; top: 290px;
    width: 580px;
    text-align: center;
    font-size: 72px;
    font-weight: 600;
    letter-spacing: 2px;
    color: var(--brand);
  }
</style>
</head>
<body>
  <div class="business-card">
    <div class="frost-disc"></div>

    <div class="contact-block">
      <div class="person-name">OWEN HARTLEY</div>
      <div class="person-role">CEO/FOUNDER</div>
      <div class="address">214 Wattle Street<br>Brisbane, QLD 4000</div>
      <ul class="contact-list">
        <li>
          <svg viewBox="0 0 24 24" aria-hidden="true"><path d="M6.6 10.8a15 15 0 0 0 6.6 6.6l2.2-2.2c.3-.3.7-.4 1-.2 1.1.4 2.3.6 3.6.6.6 0 1 .4 1 1V20c0 .6-.4 1-1 1A17 17 0 0 1 3 4c0-.6.4-1 1-1h3.5c.6 0 1 .4 1 1 0 1.3.2 2.5.6 3.6.1.3 0 .7-.2 1z"/></svg>
          07 3184 5520
        </li>
        <li>
          <svg viewBox="0 0 24 24" aria-hidden="true"><path d="M7 1h10a2 2 0 0 1 2 2v18a2 2 0 0 1-2 2H7a2 2 0 0 1-2-2V3a2 2 0 0 1 2-2zm0 3v14h10V4zm5 15.2a1 1 0 1 0 0 2 1 1 0 0 0 0-2z"/></svg>
          0412 907 336
        </li>
        <li>
          <svg viewBox="0 0 24 24" aria-hidden="true"><path d="M6 2h12v5H6zM3 8h18a2 2 0 0 1 2 2v7h-4v5H5v-5H1v-7a2 2 0 0 1 2-2zm4 8v4h10v-4z"/></svg>
          07 3184 5521
        </li>
        <li>
          <svg viewBox="0 0 24 24" aria-hidden="true"><path d="M2 5h20v14H2zm2 2v.5l8 5 8-5V7z"/></svg>
          owen@tellmora.com
        </li>
        <li>
          <svg viewBox="0 0 24 24" aria-hidden="true"><path d="M12 2a10 10 0 1 0 0 20 10 10 0 0 0 0-20zm0 2c1 1.3 1.8 3 2.1 5H9.9C10.2 7 11 5.3 12 4zM4.3 11h3.6a16 16 0 0 0 0 2H4.3a8 8 0 0 1 0-2zm5.6 0h4.2a14 14 0 0 1 0 2H9.9a14 14 0 0 1 0-2zm6.2 0h3.6a8 8 0 0 1 0 2h-3.6a16 16 0 0 0 0-2zM9.9 15h4.2c-.3 2-1.1 3.7-2.1 5-1-1.3-1.8-3-2.1-5z"/></svg>
          www.tellmora.com
        </li>
      </ul>
    </div>

    <div class="brand-name">TELLMORA</div>
  </div>
</body>
</html>
```